Business Cards for a law firm

Business cards for our law firm. Use our silhoette logo and OAK PARTNERS - check our website (www.oakpartners.example)

Contact Information for Business Card

our silhouette logo, OAK PARTNERS, 800-555-0147, Dorian Pemberton, dorian@oakpartners.example

Requirements
Must have
• our silhouette logo, OAK PARTNERS, 800-555-0147, Dorian Pemberton, dorian@oakpartners.example

```html
<!DOCTYPE html>
<html lang="en">
<head>
<meta charset="utf-8">
<title>Oak Partners — Business Cards</title>
<link href="https://fonts.googleapis.com/css2?family=Roboto:wght@400;700&display=swap" rel="stylesheet">
<style>
  :root {
    --backdrop: #959595;
    --navy: #24356b;
    --navy-deep: #1a2954;
    --orange: #f5a623;
    --white: #ffffff;
    --figure-grey: #ebebeb;
  }
  * { margin: 0; padding: 0; box-sizing: border-box; }
  html, body { width: 1200px; height: 1000px; overflow: hidden; }
  body {
    background: var(--backdrop);
    font-family: 'Roboto', Arial, sans-serif;
    position: relative;
  }
  .card {
    position: absolute;
    left: 253px;
    width: 694px;
    height: 400px;
    overflow: hidden;
  }
  .card-front { top: 61px; background: var(--navy); }
  .card-back { top: 523px; background: var(--white); }

  .front-brand {
    position: absolute;
    left: 0; right: 0; top: 0; bottom: 0;
    display: flex;
    align-items: center;
    justify-content: center;
    gap: 18px;
  }
  .front-brand .mark {
    width: 30px; height: 30px;
    background: var(--navy-deep);
  }
  .front-brand .name {
    font-weight: 700;
    font-size: 40px;
    letter-spacing: 3px;
    color: var(--navy-deep);
  }

  .back-brand {
    position: absolute;
    left: 55px; top: 70px;
    display: flex;
    align-items: center;
    gap: 12px;
  }
  .back-brand .mark {
    width: 22px; height: 22px;
    background: var(--navy);
  }
  .back-brand .name {
    font-weight: 700;
    font-size: 24px;
    letter-spacing: 2px;
    color: var(--navy);
  }

  .figures {
    position: absolute;
    left: 392px; top: 0;
    width: 272px; height: 400px;
    background: linear-gradient(180deg, var(--figure-grey), #efefef);
    border-radius: 40px 40px 0 0;
  }

  .contact {
    position: absolute;
    left: 55px; top: 230px;
    color: var(--navy);
  }
  .contact .person {
    font-weight: 700;
    font-size: 24px;
    letter-spacing: 0.3px;
  }
  .contact .person .surname { color: var(--orange); }
  .contact .email { font-size: 18px; margin-top: 2px; }
  .contact .rule {
    width: 141px; height: 3px;
    background: var(--orange);
    margin: 12px 0 14px;
  }
  .contact .line {
    display: flex; align-items: center; gap: 10px;
    font-size: 18px; line-height: 22px;
  }
  .contact .line svg { width: 13px; height: 13px; flex: none; }
</style>
</head>
<body>
  <section class="card card-front">
    <div class="front-brand">
      <span class="mark"></span>
      <span class="name">OAK PARTNERS</span>
    </div>
  </section>

  <section class="card card-back">
    <div class="back-brand">
      <span class="mark"></span>
      <span class="name">OAK PARTNERS</span>
    </div>

    <div class="figures" role="img" aria-label="Faint silhouettes of two standing men in suits"></div>

    <div class="contact">
      <div class="person">DORIAN <span class="surname">PEMBERTON</span></div>
      <div class="email">dorian@oakpartners.example</div>
      <div class="rule"></div>
      <div class="line">
        <svg viewBox="0 0 24 24" aria-hidden="true"><path fill="#f5a623" d="M6.6 10.8a15.1 15.1 0 0 0 6.6 6.6l2.2-2.2c.3-.3.7-.4 1-.2 1.1.4 2.3.6 3.6.6.6 0 1 .4 1 1V20c0 .6-.4 1-1 1A17 17 0 0 1 3 4c0-.6.4-1 1-1h3.5c.6 0 1 .4 1 1 0 1.3.2 2.5.6 3.6.1.3 0 .7-.2 1z"/></svg>
        <span>(800) 555-0147</span>
      </div>
      <div class="line">
        <svg viewBox="0 0 24 24" aria-hidden="true"><g fill="none" stroke="#f5a623" stroke-width="2"><circle cx="12" cy="12" r="9"/><path d="M3 12h18M12 3c3 3 3 15 0 18M12 3c-3 3-3 15 0 18"/></g></svg>
        <span>oakpartners.example</span>
      </div>
    </div>
  </section>
</body>
</html>
```